Business card design for holistic health care clinic

We need a double-sided business card design for our holistic health care clinic that integrates our logo design and also its color scheme. My business is called Valmira. It is an integrative medicine clinic. You have already done the logo for me. Please ensure an elegant and upscale design that is not cluttered, but still has all the necessary information (please see below for details).

Target Market(s)

Wellness, fitness, rehabilitation for educated, well-traveled open-minded clients who are focused on natural, organic, balanced and preventive healthcare and lifestyle.

Industry/Entity Type

Medical

Contact Information for Business Card

Modern, clean.

Number of Pages Required

1 page

Font styles to use
Serif
Sans Serif

Colors

Designer to choose colors to be used in the design.

Requirements
Must have
• Logo on one side, all other information on the other side.
• Other information should include:
• Tobias Wrenfeld - DOE, CPT, LMT
• 4100 East Marrow Drive
• Austin, TX 78119
• 512 555 0148
• 818 555 0192
• info@ValmiraHealth.example
• t.wrenfeld@ValmiraHealth.example
Nice to have
• Darker background on front - but not totally black - shaded/dark gray.

```html
<!DOCTYPE html>
<html lang="en">
<head>
<meta charset="utf-8">
<title>Valmira – Business Card</title>
<link href="https://fonts.googleapis.com/css2?family=Oswald:wght@500&family=Work+Sans:wght@400;500;600&display=swap" rel="stylesheet">
<style>
  :root {
    --page-bg: #161616;
    --card-bg: #2a2a2a;
    --card-edge: #333333;
    --text-light: #f2f2f2;
    --text-muted: #9a9a9a;
    --silver: #c9c9c9;
    --accent: #2aa3e0;
  }
  html, body {
    margin: 0;
    width: 1200px;
    height: 900px;
    overflow: hidden;
    background: var(--page-bg);
    font-family: "Work Sans", sans-serif;
  }
  .canvas {
    position: relative;
    width: 1200px;
    height: 900px;
  }
  .card {
    position: absolute;
    left: 270px;
    width: 660px;
    height: 377px;
    background: linear-gradient(135deg, var(--card-bg), #232323 70%, #1f1f1f);
    border: 1px solid var(--card-edge);
    box-sizing: border-box;
    color: var(--text-light);
  }
  .card--front { top: 54px; }
  .card--back { top: 468px; }

  /* Front */
  .brand {
    position: absolute;
    top: 96px;
    left: 0;
    right: 0;
    text-align: center;
  }
  .brand__name {
    font-weight: 600;
    font-size: 78px;
    letter-spacing: 2px;
    color: var(--silver);
    line-height: 1;
    text-transform: uppercase;
  }
  .brand__tagline {
    margin-top: 8px;
    font-weight: 500;
    font-size: 21px;
    letter-spacing: 1.5px;
    color: var(--text-muted);
  }
  .website {
    position: absolute;
    bottom: 50px;
    left: 0;
    right: 0;
    text-align: center;
    font-size: 15px;
    letter-spacing: 2px;
    color: var(--text-light);
  }
  .website__domain { color: var(--accent); }

  /* Back */
  .identity {
    position: absolute;
    top: 120px;
    right: 380px;
    text-align: right;
  }
  .identity__name {
    font-family: "Oswald", sans-serif;
    font-weight: 500;
    font-size: 38px;
    color: var(--accent);
    text-transform: uppercase;
    line-height: 1.05;
    white-space: nowrap;
  }
  .identity__credentials {
    margin-top: 6px;
    font-size: 17px;
    letter-spacing: 1px;
  }
  .divider {
    position: absolute;
    top: 112px;
    left: 300px;
    width: 2px;
    height: 92px;
    background: var(--accent);
  }
  .contact {
    position: absolute;
    top: 112px;
    left: 322px;
    margin: 0;
    padding: 0;
    list-style: none;
  }
  .contact__item {
    display: flex;
    align-items: center;
    gap: 10px;
    font-size: 16px;
    letter-spacing: 0.5px;
    line-height: 23px;
  }
  .contact__icon {
    width: 14px;
    height: 14px;
    fill: var(--accent);
    flex: none;
  }
  .location {
    position: absolute;
    left: 60px;
    bottom: 46px;
    font-size: 17px;
    letter-spacing: 0.8px;
  }
  .location__label { color: var(--accent); }
</style>
</head>
<body>
<main class="canvas">
  <section class="card card--front" aria-label="Card front">
    <div class="brand">
      <div class="brand__name">Valmira</div>
      <div class="brand__tagline">Integrative Holistic Medicine</div>
    </div>
    <div class="website">www.<span class="website__domain">valmirahealth</span>.example</div>
  </section>

  <section class="card card--back" aria-label="Card back">
    <div class="identity">
      <div class="identity__name">Tobias Wrenfeld</div>
      <div class="identity__credentials">DOE, CPT, LMT</div>
    </div>
    <div class="divider"></div>
    <ul class="contact">
      <li class="contact__item">
        <svg class="contact__icon" viewBox="0 0 16 16" aria-hidden="true"><path d="M3.5 1l2.5 3-1.5 2c1 2 3 4 5 5l2-1.5 3 2.5-1.5 2.5C7 15 1 9 1 2.5z"/></svg>
        512 555 0148
      </li>
      <li class="contact__item">
        <svg class="contact__icon" viewBox="0 0 16 16" aria-hidden="true"><path d="M4 0h8v16H4zM5.5 1.5v11h5v-11zM7 13.5h2v1H7z" fill-rule="evenodd"/></svg>
        818 555 0192
      </li>
      <li class="contact__item">
        <svg class="contact__icon" viewBox="0 0 16 16" aria-hidden="true"><path d="M0 3h16v10H0zM1.5 4.5L8 9l6.5-4.5v-0.1H1.5z"/></svg>
        info@ValmiraHealth.example
      </li>
      <li class="contact__item">
        <svg class="contact__icon" viewBox="0 0 16 16" aria-hidden="true"><path d="M0 3h16v10H0zM1.5 4.5L8 9l6.5-4.5v-0.1H1.5z"/></svg>
        t.wrenfeld@ValmiraHealth.example
      </li>
    </ul>
    <div class="location"><span class="location__label">Location:</span> 4100 East Marrow Drive&nbsp;&nbsp;Austin, TX 78119</div>
  </section>
</main>
</body>
</html>
```